Velmora Systems Website

Website design for our company: Velmora Systems.
The website should look fresh and IT focused. Please have a look at http://www.velmorasystems.example.au/ for our current design. We want something fresh and new, professional looking, in WordPress so we can easily make changes.

It Company

```html
<!DOCTYPE html>
<html lang="en">
<head>
<meta charset="utf-8">
<title>Velmora Systems</title>
<link rel="stylesheet" href="https://fonts.googleapis.com/css2?family=Open+Sans:wght@400;600;700&family=Arimo:ital,wght@0,400;0,700;1,400&display=swap">
<style>
:root{
  --blue:#0b62ad;
  --blue-band:#0a5c9c;
  --green:#12a84b;
  --text:#222;
  --line:#b5b5b5;
  --footer:#3b3b3b;
  --footer-box:#484848;
  --hero-dark:#061a33;
}
*{box-sizing:border-box;margin:0;padding:0}
html,body{width:953px;height:1200px;overflow:hidden}
body{position:relative;background:#fff;font-family:"Arimo",sans-serif;color:var(--text);font-size:10px}
/* header */
.site-header{position:absolute;left:0;top:0;width:953px;height:92px;border-top:2px solid var(--blue);background:linear-gradient(#fff,#f1f1f1);border-bottom:1px solid #ddd}
.brand{position:absolute;left:140px;top:16px;width:121px;height:62px;background:var(--green);border:3px solid #0d8a3c;border-radius:3px;display:flex;align-items:center;justify-content:center;gap:6px;color:#fff;font-family:"Open Sans",sans-serif;font-weight:700;font-size:12px;line-height:1.1;text-align:center}
.brand-dot{width:12px;height:12px;border-radius:50%;background:#fff;flex:none}
.search{position:absolute;left:520px;top:26px;width:147px;height:22px;border:1px solid #ccc;background:#fff;font-style:italic;font-size:10px;color:#777;padding:4px 6px}
.search svg{position:absolute;right:6px;top:4px}
.call{position:absolute;left:688px;top:22px;display:flex;gap:6px;align-items:center;font-family:"Open Sans",sans-serif}
.call small{display:block;font-size:9px;color:#333}
.call strong{display:block;font-size:15px;font-weight:400;color:#222;line-height:1}
.main-nav{position:absolute;left:309px;top:64px;display:flex;font-family:"Open Sans",sans-serif;font-size:10.5px;color:#222}
.main-nav a{color:inherit;text-decoration:none;padding:0 12px;border-left:1px solid #bbb;line-height:13px}
.main-nav a:first-child{border-left:none;color:var(--green)}
/* hero */
.hero{position:absolute;left:0;top:92px;width:953px;height:334px;background:var(--hero-dark)}
.hero-photo{position:absolute;left:140px;top:0;width:672px;height:298px;background:radial-gradient(ellipse at 50% 55%,#6d8fe6 0%,#3852b8 30%,#15246a 65%,#070f30 100%)}
.hero-arrow{position:absolute;top:150px;width:26px;height:26px;border-radius:50%;background:rgba(0,0,0,.6);display:flex;align-items:center;justify-content:center}
.hero-band{position:absolute;left:0;top:298px;width:953px;height:36px;background:var(--blue-band);color:#fff;font-family:"Open Sans",sans-serif;font-size:18.5px;text-align:center;line-height:36px}
/* sections */
.section-title{position:absolute;font-family:"Open Sans",sans-serif;font-weight:600;font-size:16.5px;color:var(--blue);border-bottom:1px dashed var(--line);padding-bottom:4px}
.pager{position:absolute;display:flex;gap:10px}
.services{position:absolute;left:140px;top:500px;width:672px;display:flex;justify-content:space-between}
.service{width:130px;text-align:center}
.service h3{font-family:"Open Sans",sans-serif;font-weight:600;font-size:10.5px;color:#222;margin-bottom:8px}
.service.active h3{color:var(--green)}
.service-ring{width:96px;height:96px;margin:0 auto;border-radius:50%;background:radial-gradient(#f4f4f4,#e2e2e2);border:2px solid #ececec;box-shadow:0 4px 5px rgba(0,0,0,.08);display:flex;align-items:center;justify-content:center}
.service.active .service-ring{background:#fff;border:4px solid var(--green)}
.service p{margin-top:14px;font-size:9.5px;line-height:14px;color:#222}
.divider{position:absolute;left:140px;top:697px;width:675px;height:1px;background:linear-gradient(90deg,transparent,#ddd,transparent)}
.about-photo{position:absolute;left:140px;top:759px;width:203px;height:93px;background:linear-gradient(100deg,#7b6a5c,#c9c2b8 40%,#3c3f48 75%,#9ea3ab)}
.body-text{position:absolute;font-size:8.1px;line-height:12.6px;color:#222;text-align:justify}
.read-more{position:absolute;font-size:9px;font-weight:700;color:var(--green)}
.quote{position:absolute;left:374px;width:208px;font-size:8.8px;line-height:14.6px;color:#222}
.quote cite{display:block;text-align:right;font-style:normal;font-weight:700;font-size:8.5px;color:#444;line-height:11px}
.q{font-family:Georgia,serif;font-size:15px;font-weight:700;line-height:0}
.field{position:absolute;left:609px;width:203px;height:21px;border:1px solid #ccc;border-radius:2px;box-shadow:inset 0 1px 2px rgba(0,0,0,.08);font-style:italic;font-size:8.5px;color:#666;padding:4px 8px}
.btn{position:absolute;background:var(--green);color:#fff;font-family:"Open Sans",sans-serif;font-weight:600;font-size:10.5px;padding:2px 8px;border-radius:2px}
.clients{position:absolute;left:140px;top:1022px;width:435px;display:flex;justify-content:space-between;align-items:center;font-family:"Open Sans",sans-serif;font-weight:700;font-size:16px;color:#555}
/* footer */
.site-footer{position:absolute;left:0;top:1085px;width:953px;height:115px;background:var(--footer);border-top:2px solid #222;color:#fff;font-family:"Open Sans",sans-serif}
.f-box{position:absolute;top:13px;height:58px;background:var(--footer-box);border:1px solid #555;padding:6px 9px}
.f-box h4{font-weight:600;font-size:10.5px;margin-bottom:6px}
.f-line{display:flex;align-items:center;gap:6px;font-family:"Arimo",sans-serif;font-size:8.5px;margin-bottom:4px;white-space:nowrap}
.social{display:flex;gap:11px}
.social span{width:19px;height:19px;border-radius:3px}
.f-brand{position:absolute;left:692px;top:12px;width:121px;height:62px;background:var(--green);border:3px solid #fff;border-radius:3px;display:flex;align-items:center;justify-content:center;gap:6px;font-weight:700;font-size:12px;line-height:1.1;text-align:center}
.f-nav{position:absolute;left:140px;top:93px;font-family:"Arimo",sans-serif;font-size:8.5px}
.f-nav a{color:#fff;text-decoration:none}
.f-nav a:first-child{color:var(--green)}
.f-nav i{font-style:normal;margin:0 4px}
.copy{position:absolute;left:611px;top:93px;font-family:"Arimo",sans-serif;font-size:8.5px}
</style>
</head>
<body>

<header class="site-header">
  <div class="brand"><span class="brand-dot"></span><span>Velmora<br>Systems</span></div>
  <div class="search">search
    <svg width="12" height="12" viewBox="0 0 12 12"><circle cx="5" cy="5" r="3.6" fill="none" stroke="#777" stroke-width="1.5"/><path d="M7.7 7.7L11 11" stroke="#777" stroke-width="1.6"/></svg>
  </div>
  <div class="call">
    <svg width="22" height="22" viewBox="0 0 22 22"><circle cx="11" cy="11" r="10" fill="none" stroke="#12a84b" stroke-width="1.5"/><path d="M8 5c-1 1-1.5 2-1 4 .8 3 3 5.6 6 6.5 1.6.4 2.4 0 3.2-.9l-2-2-1.4.8c-1.4-.6-2.7-2-3.2-3.4l.8-1.4z" fill="#12a84b"/></svg>
    <div><small>Call Us Today</small><strong>555 318 2046</strong></div>
  </div>
  <nav class="main-nav">
    <a href="#">HOME</a><a href="#">ABOUT US</a><a href="#">SERVICES</a><a href="#">SUPPORT</a><a href="#">TESTIMONIALS</a><a href="#">CLIENTS</a><a href="#">CONTACT US</a>
  </nav>
</header>

<section class="hero">
  <div class="hero-photo" role="img" aria-label="Photo of a data centre corridor lined with server racks in blue light"></div>
  <div class="hero-arrow" style="left:144px"><svg width="8" height="12" viewBox="0 0 8 12"><path d="M6 1L1 6l5 5" fill="none" stroke="#fff" stroke-width="1.4"/></svg></div>
  <div class="hero-arrow" style="left:782px"><svg width="8" height="12" viewBox="0 0 8 12"><path d="M2 1l5 5-5 5" fill="none" stroke="#fff" stroke-width="1.4"/></svg></div>
  <div class="hero-band">WE HAVE SPECIALISED ENGINEERS, TRAINED TO DO SPECIALISED WORK</div>
</section>

<h2 class="section-title" style="left:143px;top:457px;width:670px">Our Services</h2>
<div class="pager" style="left:783px;top:465px">
  <svg width="7" height="11" viewBox="0 0 7 11"><path d="M6 1L1 5.5 6 10" fill="none" stroke="#555" stroke-width="1.3"/></svg>
  <svg width="7" height="11" viewBox="0 0 7 11"><path d="M1 1l5 4.5L1 10" fill="none" stroke="#12a84b" stroke-width="1.3"/></svg>
</div>

<div class="services">
  <div class="service active"><h3>On-site Service</h3>
    <div class="service-ring"><svg width="46" height="46" viewBox="0 0 46 46" fill="#12a84b"><rect x="20" y="4" width="6" height="38" rx="2" transform="rotate(45 23 23)"/><rect x="20" y="4" width="6" height="38" rx="2" transform="rotate(-45 23 23)"/><rect x="8" y="5" width="14" height="8" rx="2" transform="rotate(-45 15 9)"/></svg></div>
    <p>Lorem ipsum dolor sit amet ummy nibh eui smod</p></div>
  <div class="service"><h3>Remote Desktop</h3>
    <div class="service-ring"><svg width="50" height="46" viewBox="0 0 50 46" fill="none" stroke="#555" stroke-width="3"><rect x="3" y="6" width="32" height="22"/><path d="M14 36h12M20 28v8"/><circle cx="34" cy="30" r="11" fill="#eee"/><path d="M29 28h10l-3-3M39 32H29l3 3" stroke-width="2"/></svg></div>
    <p>Lorem ipsum dolor sit amet ummy nibh eui smod</p></div>
  <div class="service"><h3>Medical IT Service</h3>
    <div class="service-ring"><svg width="50" height="46" viewBox="0 0 50 46" fill="none" stroke="#555" stroke-width="3"><path d="M8 6v12c0 7 12 7 12 0V6"/><path d="M14 24v8c0 8 14 8 14 0v-4"/><circle cx="28" cy="24" r="4"/><circle cx="38" cy="14" r="5"/></svg></div>
    <p>Lorem ipsum dolor sit amet ummy nibh eui smod</p></div>
  <div class="service"><h3>Pharmacy IT</h3>
    <div class="service-ring"><svg width="50" height="46" viewBox="0 0 50 46" fill="none" stroke="#555" stroke-width="3"><rect x="5" y="5" width="34" height="28"/><path d="M10 25l7-8 6 5 8-9"/><circle cx="33" cy="30" r="7" fill="#eee"/><path d="M38 35l6 6"/></svg></div>
    <p>Lorem ipsum dolor sit amet ummy nibh eui smod</p></div>
  <div class="service"><h3>Website Design</h3>
    <div class="service-ring"><svg width="50" height="46" viewBox="0 0 50 46" fill="none" stroke="#555" stroke-width="3"><rect x="6" y="8" width="38" height="24"/><path d="M18 40h14M25 32v8M20 26l14-14"/></svg></div>
    <p>Lorem ipsum dolor sit amet ummy nibh eui smod</p></div>
</div>

<div class="divider"></div>

<h2 class="section-title" style="left:141px;top:726px;width:204px">About Velmora Systems</h2>
<div class="about-photo" role="img" aria-label="Photo of a business team meeting around a laptop"></div>
<p class="body-text" style="left:141px;top:857px;width:202px">Velmora Systems is an Adelaide based company with a single objective - to excel in the support and service of all computer and IT needs. We provide a high level of consulting services using the most experienced engineers at a reasonable and fair price. We believe in using a Business Value approach to every</p>
<span class="read-more" style="left:288px;top:938px">Read More »</span>

<h2 class="section-title" style="left:373px;top:726px;width:204px">Client Testimonials</h2>
<div class="quote" style="top:762px"><span class="q">“</span> Nonummy nibh uismod tincidunt ut laoreet dolore magna aliquam erat volutpat. Ut wisi enim ad minim nonummy nibh euismod tincidunt <span class="q">”</span><cite>Corin Aldwell - NRT</cite></div>
<div class="quote" style="top:825px"><span class="q">“</span> I have always found the team extremely helpful with their advice over the phone. They also have the ability to access our computers remotely, and can rectify most problems quite swiftly. I have no hesitation in recommending Velmora Systems for all of your IT needs.<span class="q">”</span><cite>Marcus Tellender B.Pharm<br>Brightwell Family Pharmacy, Elm Vale</cite></div>
<span class="read-more" style="left:529px;top:938px">Read More »</span>

<h2 class="section-title" style="left:608px;top:726px;width:204px">Quick Contact</h2>
<div class="field" style="top:760px">Name</div>
<div class="field" style="top:792px">Email</div>
<div class="field" style="top:824px">Phone</div>
<div class="field" style="top:856px;height:61px">Message</div>
<span class="btn" style="left:610px;top:928px">Submit</span>

<h2 class="section-title" style="left:140px;top:979px;width:436px">Our Clients</h2>
<div class="pager" style="left:558px;top:986px">
  <svg width="7" height="11" viewBox="0 0 7 11"><path d="M6 1L1 5.5 6 10" fill="none" stroke="#555" stroke-width="1.3"/></svg>
  <svg width="7" height="11" viewBox="0 0 7 11"><path d="M1 1l5 4.5L1 10" fill="none" stroke="#12a84b" stroke-width="1.3"/></svg>
</div>
<div class="clients"><span>Northgrid</span><span>cloudvane</span><span>KORRA</span><span>Lumetra</span></div>

<h2 class="section-title" style="left:604px;top:980px;width:208px">Remote Support</h2>
<div class="field" style="left:604px;top:1013px;width:203px">Enter your 6 digit code</div>
<span class="btn" style="left:605px;top:1040px">Connect Now</span>

<footer class="site-footer">
  <div class="f-box" style="left:139px;width:185px">
    <h4>Subscribe to Newsletter</h4>
    <div style="display:flex;gap:6px">
      <div style="width:135px;height:21px;background:#5c5c5c;font-family:'Arimo',sans-serif;font-style:italic;font-size:8.5px;padding:5px 8px">Email here</div>
      <div style="width:23px;height:21px;background:#5c5c5c;display:flex;align-items:center;justify-content:center"><svg width="7" height="10" viewBox="0 0 7 10"><path d="M1 1l4 4-4 4" fill="none" stroke="#fff" stroke-width="2"/></svg></div>
    </div>
  </div>
  <div class="f-box" style="left:363px;width:163px">
    <h4>Contact Us</h4>
    <div class="f-line"><svg width="9" height="9" viewBox="0 0 9 9"><path d="M1.5 1c-1 1 0 4 2.5 6s4 2 5 1L7.5 6.5 6 7.2C5 6.7 2.8 4.6 2.3 3.5L3 2z" fill="#fff"/></svg>555 318 2046</div>
    <div class="f-line"><svg width="10" height="8" viewBox="0 0 10 8"><rect width="10" height="8" fill="#fff"/><path d="M0 0l5 4 5-4" fill="none" stroke="#484848"/></svg>help@velmora.example.au</div>
  </div>
  <div class="f-box" style="left:564px;width:89px">
    <h4>Follow Us</h4>
    <div class="social"><span style="background:#3b5b9a"></span><span style="background:#4fa8d8"></span><span style="background:#e8721c"></span></div>
  </div>
  <div class="f-brand"><span class="brand-dot"></span><span>Velmora<br>Systems</span></div>
  <nav class="f-nav"><a href="#">Home</a><i>|</i><a href="#">About Us</a><i>|</i><a href="#">Services</a><i>|</i><a href="#">Support</a><i>|</i><a href="#">Testimonials</a><i>|</i><a href="#">Clients</a><i>|</i><a href="#">Contact Us</a><i>|</i><a href="#">Terms Conditions</a></nav>
  <p class="copy">Copyright © 2014 &nbsp;velmorasystems. &nbsp;All Rights Reserved</p>
</footer>

</body>
</html>
```